Finiding oppertunites in Real Estate 6.15.20

size of ad 7” x 9.6”
1-I like the ad to stand out and attract people's attention.
2-you should be able to see the text of the ad clearly .. see the attachment anything in yellow is instructions.
3-the list of topics should not be the main part of the ad
4-if you decide you want a picture or vector of a person .. (you decide)
then it should be a white male about 25-30 years old wearing a solid white or blue shirt and not long hair.
5-leave 1 inch for footer
see attachment
Good luck

Target Market(s)

potential male students 25-35 years of age

Industry/Entity Type

Education

Requirements
Must have
• will stand out and people would want to see it.
should be able to read the words of ad
Nice to have
• how to make money in real estate on one line

```html
<!DOCTYPE html>
<html lang="en">
<head>
<meta charset="utf-8">
<title>Real Estate Career Course</title>
<link rel="stylesheet" href="https://fonts.googleapis.com/css2?family=Open+Sans:wght@400;600;700;800&display=swap">
<style>
  :root {
    --page-bg: #e9e9ea;
    --paper: #ffffff;
    --ink-dark: #4a4a4c;
    --ink-mid: #5a5a5c;
    --ink-soft: #6b6b6d;
    --accent-blue: #11a3e4;
    --accent-red: #ec565d;
    --accent-red-edge: #d8434a;
    --rule-dark: #555557;
    --dash: #8a8a8c;
    --halftone-a: #e4e4e6;
    --halftone-b: #ffffff;
    --photo-a: #f2f2f2;
    --photo-b: #d9d9db;
  }
  * { box-sizing: border-box; margin: 0; padding: 0; }
  html, body {
    width: 743px; height: 1200px; overflow: hidden;
    background: var(--page-bg);
    font-family: "Open Sans", Arial, sans-serif;
  }
  .flyer {
    position: absolute; left: 21px; top: 120px;
    width: 700px; height: 960px;
    background: var(--paper);
    overflow: hidden;
    box-shadow: 0 6px 18px rgba(0,0,0,.12);
  }
  .flyer__texture {
    position: absolute; right: 0; top: 0;
    width: 330px; height: 620px;
    background: radial-gradient(ellipse at 85% 25%, var(--halftone-a) 0%, rgba(228,228,230,.5) 40%, rgba(255,255,255,0) 72%);
  }
  .centered { position: absolute; left: 0; width: 100%; text-align: center; white-space: nowrap; }
  .title {
    top: 53px; font-size: 36px; font-weight: 800; color: var(--ink-mid); line-height: 44px;
  }
  .headline {
    font-size: 34px; line-height: 42px; color: var(--ink-mid); font-weight: 400;
  }
  .headline--one { top: 117px; }
  .headline--two { top: 160px; }
  .headline strong { font-weight: 800; color: var(--ink-dark); }
  .headline .money { font-weight: 800; color: var(--accent-blue); }

  .audience {
    position: absolute; left: 54px; top: 221px; width: 592px; height: 73px;
    border: 1.5px dashed var(--dash); border-radius: 10px;
    display: flex; align-items: center;
  }
  .audience__col {
    flex: 1; font-size: 18px; line-height: 24px; color: var(--ink-soft);
  }
  .audience__col--left { text-align: right; padding-right: 18px; }
  .audience__col--right { text-align: right; padding-right: 14px; padding-left: 18px; }
  .audience__divider { width: 2px; height: 50px; background: var(--accent-blue); }
  .audience b { font-weight: 700; color: var(--ink-dark); }
  .audience .hl { font-weight: 700; color: var(--accent-blue); }

  .sessions-pill {
    position: absolute; left: 218px; top: 311px; width: 263px; height: 50px;
    background: var(--accent-red); border: 2px solid var(--accent-red-edge);
    border-radius: 9px; color: #fff;
    font-size: 25px; font-weight: 700; text-align: center; line-height: 46px;
  }
  .course-length {
    top: 372px; font-size: 23px; font-weight: 700; color: var(--ink-mid); line-height: 32px;
  }
  .start-date {
    position: absolute; left: 206px; top: 414px; width: 286px; height: 42px;
    border: 1.5px solid var(--ink-mid); border-radius: 7px; overflow: hidden;
    display: flex; font-size: 21px; font-weight: 700; line-height: 39px;
  }
  .start-date__label { width: 187px; text-align: center; color: var(--ink-mid); }
  .start-date__value { flex: 1; text-align: center; color: #fff; background: var(--accent-blue); }

  .topics-heading {
    top: 471px; font-size: 21px; font-weight: 700; color: var(--accent-blue); line-height: 28px;
  }
  .topics-rule {
    position: absolute; left: 332px; top: 503px; width: 36px; height: 3px; background: var(--rule-dark);
  }
  .topics-list {
    top: 513px; font-size: 11px; line-height: 15px; color: var(--ink-dark);
  }
  .photo {
    position: absolute; left: 163px; top: 569px; width: 361px; height: 300px;
    background: radial-gradient(ellipse at 50% 50%, var(--photo-b) 0%, var(--photo-a) 60%, rgba(255,255,255,0) 80%);
  }
</style>
</head>
<body>
  <main class="flyer">
    <div class="flyer__texture" role="img" aria-label="Soft grey halftone dot texture"></div>

    <h1 class="centered title">Real Estate Career Course</h1>
    <p class="centered headline headline--one">How to <span class="money">Make Money</span></p>
    <p class="centered headline headline--two">in <strong>Real Estate?</strong></p>

    <section class="audience">
      <p class="audience__col audience__col--left">For those who have started or<br>would like to go into <span class="hl">Real Estate</span></p>
      <span class="audience__divider"></span>
      <p class="audience__col audience__col--right">An <b>investment in knowledge</b><br>opens up untold <span class="hl">opportunities</span></p>
    </section>

    <div class="sessions-pill">Remote sessions</div>
    <p class="centered course-length">12 session course</p>
    <div class="start-date">
      <span class="start-date__label">Classes starting</span>
      <span class="start-date__value">June 16</span>
    </div>

    <h2 class="centered topics-heading">A partial listing of Topics</h2>
    <span class="topics-rule"></span>
    <p class="centered topics-list">
      Single-family | Multifamily | Management | Real Estate Concepts | Real Estate law | Investment<br>
      properties | Foreclosures Rehab | &nbsp;Foreclosures | Short sales | Development | Finical modeling<br>
      HUD properties | Due Diligence e
    </p>

    <div class="photo" role="img" aria-label="Photo of a smiling young man in a white t-shirt and black jeans sitting cross-legged, giving two thumbs up"></div>
  </main>
</body>
</html>
```